Business Card Design

We require a business card design for a law firm, our signature colours are maroon and cream. Our slogan is "From our family to yours", we would like the cards to be professional however feminine at the same time.

Industry/Entity Type

Business

Contact Information for Business Card

Helena Drace & Associates Lawyers & Conveyancers, Helena Drace LL.B. Principal Solicitor, 17 Kellow Street, Marrick NSW 2299

Logo styles of interest
Emblem Logo
Abstract Logo
Wordmark Logo

```html
<!DOCTYPE html>
<html lang="en">
<head>
<meta charset="utf-8">
<title>Helena Drace &amp; Associates – Business Card</title>
<link rel="stylesheet" href="https://fonts.googleapis.com/css2?family=Dancing+Script:wght@500&family=Tinos&display=swap">
<style>
  :root {
    --maroon: #7e1912;
    --cream: #fbf6d0;
    --emblem-tone: #9a3a2a;
  }
  * { margin: 0; padding: 0; box-sizing: border-box; }
  html, body {
    width: 1200px;
    height: 726px;
    overflow: hidden;
    background: var(--maroon);
  }
  .card {
    position: relative;
    width: 1200px;
    height: 726px;
    background: var(--maroon);
    color: var(--cream);
  }
  .emblem {
    position: absolute;
    left: 184px;
    top: 20px;
    width: 307px;
    height: 306px;
    border-radius: 6px;
    background: radial-gradient(ellipse at center, var(--emblem-tone) 0%, var(--maroon) 75%);
  }
  .firm-name {
    position: absolute;
    left: 18px;
    top: 344px;
    width: 600px;
    text-align: center;
    font-family: "Tinos", "Times New Roman", serif;
    font-size: 38px;
    line-height: 55px;
  }
  .script {
    position: absolute;
    font-family: "Dancing Script", cursive;
    font-weight: 500;
    white-space: nowrap;
  }
  .slogan {
    left: 720px;
    top: 38px;
    font-size: 42px;
  }
  .person {
    left: 44px;
    top: 530px;
    font-size: 52px;
    line-height: 70px;
  }
  .person .name { padding-left: 14px; display: block; }
  .address {
    left: 746px;
    top: 530px;
    font-size: 52px;
    line-height: 70px;
  }
</style>
</head>
<body>
  <div class="card">
    <div class="emblem" role="img" aria-label="Firm emblem: ornamental scales of justice with scrolling base"></div>

    <p class="firm-name">Helena Drace &amp; Associates<br>Lawyers &amp; Conveyancers</p>

    <p class="script slogan">From our family to yours</p>

    <p class="script person">
      <span class="name">Helena Drace LL.B.</span>
      <span class="role">Principal Solicitor</span>
    </p>

    <p class="script address">17 Kellow Street,<br>Marrick NSW 2299</p>
  </div>
</body>
</html>
```